Coral Wing Flights brochure

A single A4 brochures that is tri-folded and shows some of our tour packages with contact details.

Please visit www.coralwingflights.com.au to see the designs and images that can be used.

I want to provide designers the freedom to try something creative because I want to give prospective client - normally tourists to Sydney a quality service. I want the brochure to reflect this.

The image on the front page needs to be of the Sydney Harbour. The image MUST be in daylight - not night time.

I have now provided an image of the aircraft (in GIF format). Please use this image and place it over the image of the sydney harbour bridge and quayside concert pavilion.

I may need to discuss this further but what I have not show in the attached files is a small form I will like the client to fill out..

Reservation number
Name
Address
Phone number
Email

We can discuss this at a latter time.

The QR Code needs to contain your web address (www.coralwingflights.com.au)

Target Market(s)

Visitors and tourists to Sydney who want a day trip.
We are providing an exciting way to see Sydney. By air in a light aircraft...

Industry/Entity Type

House

Font styles to use
Sans Serif
Script

Colors
33a6d7
3276b5
85acd3
85cae6
ffffff

Requirements
Must have
• Brochure must be A4 (with about 2 to 3mm bleed - so it can be cut at the printers). They but be folded in 3 to produce a DL size brochure.

The words "Prepare to be amazed" should be in script font...

Please use the following wording for our Terms can conditions...

Terms and Conditions
Coral Wing Flights operates from Merrowdale Airfield within Sydney’s busy airspace Your chosen flight may be subject to delays. Clearance to enter controlled airspace may be refused - this is especially true of our popular Coastline Panorama flight. If this happens, we can either offer other suitable flights, reschedule the flight or, if this isn’t suitable, we provide a refund.
Other aircraft, besides our standard Talbin Skyrunners, are available if we consider they better suit your requirements.
See our web site www.coralwingflights.com.au for full details.
Coral Wing Flights is a trading name of Orvexa Pty Limited
(ABN 81 417 286 309) which operates under the Air Operators Certificate (AOC) of Dorrigan and Welsford Pty Ltd.
Nice to have
• Suggestion - on one of the sides (with the packages) to have a background image.

Suggestion is to keep the brochure light and "airy"

```html
<!DOCTYPE html>
<html lang="en">
<head>
<meta charset="utf-8">
<title>Coral Wing Flights – Scenic Tours</title>
<link href="https://fonts.googleapis.com/css2?family=Open+Sans:wght@300;400;600&family=Yellowtail&display=swap" rel="stylesheet">
<style>
  :root {
    --sky-blue: #33a6d7;
    --deep-blue: #3276b5;
    --soft-blue: #85acd3;
    --pale-blue: #85cae6;
    --white: #ffffff;
    --ink: #111111;
  }
  * { box-sizing: border-box; margin: 0; padding: 0; }
  html, body { width: 1200px; height: 849px; overflow: hidden; background: var(--white); }
  .brochure-inside {
    position: relative;
    width: 1200px;
    height: 849px;
    overflow: hidden;
    background: var(--white);
    font-family: "Open Sans", Arial, sans-serif;
  }
  .intro-strip {
    position: absolute; top: 0; left: 0; width: 1200px; height: 103px;
    display: flex;
  }
  .intro-text {
    width: 400px;
    padding: 17px 14px 0 18px;
    text-align: center;
    font-family: "Yellowtail", cursive;
    font-size: 14px;
    line-height: 19px;
    color: var(--ink);
  }
  .rule { position: absolute; top: 103px; left: 0; width: 1200px; height: 3px; background: var(--deep-blue); }
  .photo-row { position: absolute; top: 113px; left: 0; width: 1200px; height: 270px; display: flex; }
  .photo { width: 400px; height: 100%; }
  .photo--harbour { background: linear-gradient(170deg, #9aa7ad 0%, #6c7a74 30%, #3f6f73 60%, #2f5a5e 100%); }
  .photo--coast { background: linear-gradient(180deg, #4c8fd0 0%, #a9c9e6 35%, #5f7f5a 52%, #1d4f86 70%, #153c6e 100%); }
  .photo--mountains { background: linear-gradient(180deg, #6d86b8 0%, #b49aa8 25%, #c27b3a 50%, #4d5a2c 80%, #2f3e22 100%); }
  .wave { position: absolute; top: 0; left: 0; }
  .tour-columns { position: absolute; top: 0; left: 0; width: 1200px; height: 849px; }
  .tour-meta {
    position: absolute; top: 436px;
    color: var(--white); font-size: 15px; line-height: 23px;
  }
  .tour-meta p { display: flex; align-items: center; gap: 5px; }
  .tour-meta strong { font-weight: 600; }
  .tour-meta svg { flex: none; }
  .tour-title {
    position: absolute; top: 514px; height: 29px;
    background: var(--ink); color: var(--white);
    font-weight: 300; font-size: 18px; line-height: 29px;
    padding: 0 10px 0 17px;
  }
  .stop-list {
    position: absolute; top: 562px; list-style: none;
    color: var(--white); font-size: 15px; line-height: 21.4px;
  }
  .stop-list li { position: relative; padding-left: 17px; }
  .stop-list li svg { position: absolute; left: 0; top: 5px; }
  .footer-band { position: absolute; left: 0; bottom: 0; width: 1200px; height: 32px; background: var(--deep-blue); }
</style>
</head>
<body>
<main class="brochure-inside">
  <section class="intro-strip">
    <p class="intro-text">This is one of our most popular scenic tours because it showcases Sydneys magnificent coastline and world famous beaches. The Sydney coastal flight takes you past many well known coastal land-marks and beaches such as Maroubra Beach</p>
    <p class="intro-text">This is one of our most popular scenic tours because it showcases Sydneys magnificent coastline and world famous beaches. The Sydney coastal flight takes you past many well known coastal land-marks and beaches such as Maroubra Beach</p>
    <p class="intro-text">This is one of our most popular scenic tours because it showcases Sydneys magnificent coastline and world famous beaches. The Sydney coastal flight takes you past many well known coastal land-marks and beaches such as Maroubra Beach</p>
  </section>
  <div class="rule"></div>

  <div class="photo-row">
    <div class="photo photo--harbour" role="img" aria-label="Aerial view of Sydney Harbour, the city skyline, the bridge and the concert pavilion"></div>
    <div class="photo photo--coast" role="img" aria-label="Sydney coastline with sandstone cliffs and deep blue ocean"></div>
    <div class="photo photo--mountains" role="img" aria-label="The Three Sisters rock formation in the Blue Mountains at sunset"></div>
  </div>

  <svg class="wave" width="1200" height="849" viewBox="0 0 1200 849" aria-hidden="true">
    <path d="M0 352 C300 326 520 388 760 392 C960 395 1100 340 1200 326 L1200 849 L0 849 Z" fill="var(--deep-blue)"/>
    <path d="M0 372 C300 346 520 398 760 402 C960 405 1100 352 1200 340 L1200 849 L0 849 Z" fill="var(--white)"/>
    <path d="M0 392 C300 364 520 410 760 414 C960 416 1100 368 1200 356 L1200 849 L0 849 Z" fill="var(--sky-blue)"/>
  </svg>

  <section class="tour-columns">
    <div class="tour-meta" style="left:170px">
      <p><svg width="11" height="11" viewBox="0 0 12 12"><circle cx="6" cy="6" r="5" fill="none" stroke="#fff" stroke-width="1.4"/><path d="M6 3v3.3h2.4" fill="none" stroke="#fff" stroke-width="1.3"/></svg><strong>Duration:</strong> 1 hour 20 mins</p>
      <p><svg width="12" height="12" viewBox="0 0 12 12"><path d="M1 1h5l5 5-5 5-5-5z" fill="#fff"/><circle cx="3.5" cy="3.5" r="1" fill="var(--sky-blue)"/></svg><strong>Price:</strong> $560 per aircraft</p>
    </div>
    <div class="tour-meta" style="left:569px">
      <p><svg width="11" height="11" viewBox="0 0 12 12"><circle cx="6" cy="6" r="5" fill="none" stroke="#fff" stroke-width="1.4"/><path d="M6 3v3.3h2.4" fill="none" stroke="#fff" stroke-width="1.3"/></svg><strong>Duration:</strong> 1 hour 20 mins</p>
      <p><svg width="12" height="12" viewBox="0 0 12 12"><path d="M1 1h5l5 5-5 5-5-5z" fill="#fff"/><circle cx="3.5" cy="3.5" r="1" fill="var(--sky-blue)"/></svg><strong>Price:</strong> $560 per aircraft</p>
    </div>
    <div class="tour-meta" style="left:979px">
      <p><svg width="11" height="11" viewBox="0 0 12 12"><circle cx="6" cy="6" r="5" fill="none" stroke="#fff" stroke-width="1.4"/><path d="M6 3v3.3h2.4" fill="none" stroke="#fff" stroke-width="1.3"/></svg><strong>Duration:</strong> 1 hour 10 mins</p>
      <p><svg width="12" height="12" viewBox="0 0 12 12"><path d="M1 1h5l5 5-5 5-5-5z" fill="#fff"/><circle cx="3.5" cy="3.5" r="1" fill="var(--sky-blue)"/></svg><strong>Price:</strong> $475 per aircraft</p>
    </div>

    <h2 class="tour-title" style="left:0">Sydney Harbour Scenic</h2>
    <h2 class="tour-title" style="left:400px">Sydney Coastal</h2>
    <h2 class="tour-title" style="left:800px">The Blue Mountains</h2>

    <svg width="0" height="0" style="position:absolute">
      <symbol id="plane-icon" viewBox="0 0 12 12">
        <rect width="12" height="12" fill="var(--ink)"/>
        <path d="M9.6 2.4 2.3 6.1l2.2.7L5.3 9.5 6.5 7.4l2 1.2z" fill="var(--white)"/>
      </symbol>
    </svg>

    <ul class="stop-list" style="left:24px">
      <li><svg width="11" height="11"><use href="#plane-icon"/></svg>Parramatta City</li>
      <li><svg width="11" height="11"><use href="#plane-icon"/></svg>Hornsby</li>
      <li><svg width="11" height="11"><use href="#plane-icon"/></svg>Bahai Temple</li>
      <li><svg width="11" height="11"><use href="#plane-icon"/></svg>Sydney Harbour Bridge</li>
      <li><svg width="11" height="11"><use href="#plane-icon"/></svg>Quayside Concert Pavilion</li>
      <li><svg width="11" height="11"><use href="#plane-icon"/></svg>Manly</li>
      <li><svg width="11" height="11"><use href="#plane-icon"/></svg>Long Reef</li>
    </ul>
    <ul class="stop-list" style="left:428px">
      <li><svg width="11" height="11"><use href="#plane-icon"/></svg>Cambelltown</li>
      <li><svg width="11" height="11"><use href="#plane-icon"/></svg>Stanwell Park</li>
      <li><svg width="11" height="11"><use href="#plane-icon"/></svg>Entrance of Port Hacking</li>
      <li><svg width="11" height="11"><use href="#plane-icon"/></svg>Entrance of Botany Bay</li>
      <li><svg width="11" height="11"><use href="#plane-icon"/></svg>Famous Sydney Beaches including<br>Maroubra, Cooge, Bondi &amp; Manly</li>
      <li><svg width="11" height="11"><use href="#plane-icon"/></svg>Sydney Heads</li>
      <li><svg width="11" height="11"><use href="#plane-icon"/></svg>Long Reef</li>
    </ul>
    <ul class="stop-list" style="left:830px">
      <li><svg width="11" height="11"><use href="#plane-icon"/></svg>Katoomba</li>
      <li><svg width="11" height="11"><use href="#plane-icon"/></svg>The Three Sisters</li>
      <li><svg width="11" height="11"><use href="#plane-icon"/></svg>Warragamba Dam</li>
      <li><svg width="11" height="11"><use href="#plane-icon"/></svg>Prospect Resrvour</li>
    </ul>
  </section>

  <div class="footer-band"></div>
</main>
</body>
</html>
```